DANCE STUDIO RECITAL FLYER DESIGN 2022

I am looking for a flyer for a dance recital that encapsulates the theme of the flyer. The rhetorical answer to "Where the River Bends Home..." is Hold Me Near but I would like this to be inferred in the design of the flyer. I am looking for something uplifting and positive through the design...I don't know what I am looking for but it needs to be vibrant, heartwarming, and emotional...maybe the world can be dipped in a heart or something with butterflies???

Here are the details...

Brightwing Dance Studio presents
Our 11th Annual Recital, "Where The River Bends Home..."
Saturday, June 25, at 4 pm
Kestrel Ridge High School 31857 Marlow Road
Novi, Mi 48291

```html
<!DOCTYPE html>
<html lang="en">
<head>
<meta charset="utf-8">
<title>Brightwing Dance Studio — 11th Annual Recital</title>
<link rel="stylesheet" href="https://fonts.googleapis.com/css2?family=Roboto+Condensed:wght@400&family=Montserrat:ital,wght@0,600;0,700;0,800;1,700&family=Kaushan+Script&family=Rubik+Dirt&display=swap">
<style>
  :root {
    --stage: #6a6a6c;
    --canvas-top: #8c6a5e;
    --canvas-mid: #6e4a47;
    --canvas-deep: #4a2830;
    --gold: #f4e27a;
    --cream: #f4e6bd;
    --white: #ffffff;
    --ink: #1c1c1c;
    --venue-red: #9b1432;
    --brand-gold: #d8a236;
    --photo-skin: #c98a6c;
    --photo-heart: #b3242a;
    --photo-wing: #f2cf62;
  }
  * { box-sizing: border-box; margin: 0; padding: 0; }
  html, body { width: 1200px; height: 1200px; overflow: hidden; }
  body { background: var(--stage); position: relative; }

  .flyer {
    position: absolute; left: 191px; top: 20px;
    width: 818px; height: 1160px; overflow: hidden;
    background:
      radial-gradient(ellipse at 30% 20%, rgba(255,220,200,0.18), transparent 60%),
      linear-gradient(180deg, var(--canvas-top) 0%, var(--canvas-mid) 50%, var(--canvas-deep) 85%);
    box-shadow: 0 10px 30px rgba(0,0,0,0.35);
  }

  .hero-photo {
    position: absolute; left: 410px; top: 0; width: 408px; height: 1000px;
    background:
      radial-gradient(circle at 52% 33%, var(--photo-heart) 0 9%, transparent 10%),
      radial-gradient(ellipse at 55% 38%, var(--photo-skin) 0 30%, transparent 55%),
      radial-gradient(ellipse at 40% 78%, rgba(242,207,98,0.55) 0 14%, transparent 32%),
      linear-gradient(180deg, rgba(201,138,108,0.35), rgba(74,40,48,0.2));
    -webkit-mask-image: linear-gradient(90deg, transparent 0%, #000 30%);
    mask-image: linear-gradient(90deg, transparent 0%, #000 30%);
  }

  .headline { position: absolute; left: 0; width: 465px; text-align: center; white-space: nowrap; }

  .presenter {
    top: 58px; font-family: "Roboto Condensed", sans-serif; font-size: 42px;
    color: var(--gold);
  }
  .presents {
    top: 122px; font-family: "Montserrat", sans-serif; font-weight: 700;
    font-size: 27px; letter-spacing: 7px; color: var(--white);
  }
  .edition {
    top: 196px; font-family: "Kaushan Script", cursive; font-size: 50px;
    color: var(--gold); line-height: 60px; font-weight: 400;
  }
  .title {
    top: 415px; font-family: "Rubik Dirt", sans-serif; font-size: 58px; font-weight: 400;
    line-height: 80px; color: var(--cream); text-transform: uppercase;
    text-shadow: 0 2px 4px rgba(0,0,0,0.35);
  }
  .when {
    top: 710px; font-family: "Montserrat", sans-serif; font-weight: 700;
    font-size: 36px; line-height: 49px; color: var(--cream);
  }
  .when .day { font-style: italic; }
  .when .date { color: var(--gold); font-size: 38px; }
  .when .time { font-weight: 600; color: var(--white); }

  .paper-edge { position: absolute; left: 0; top: 840px; width: 818px; height: 320px; }

  .venue { position: absolute; left: 10px; top: 1068px; width: 450px; text-align: center;
    font-family: "Montserrat", sans-serif; }
  .venue-name { font-weight: 800; font-size: 25px; color: var(--venue-red); text-transform: uppercase; letter-spacing: -0.3px; white-space: nowrap; }
  .venue-address { font-weight: 600; font-size: 22px; color: var(--ink); margin-top: 6px; white-space: nowrap; }

  .studio-mark { position: absolute; left: 478px; top: 1000px; width: 300px; text-align: center; }
  .studio-dot { display: block; width: 40px; height: 40px; border-radius: 50%;
    background: var(--brand-gold); margin: 0 auto 14px; }
  .studio-name { font-family: "Montserrat", sans-serif; font-weight: 700; font-size: 26px;
    line-height: 32px; color: var(--brand-gold); }
</style>
</head>
<body>
  <main class="flyer">
    <div class="hero-photo" role="img" aria-label="Photo of family hands cupping a glossy red heart, with golden butterflies drifting down"></div>

    <p class="headline presenter">Brightwing Dance Studio</p>
    <p class="headline presents">PRESENTS</p>
    <h2 class="headline edition">11 th<br>Annual Recital</h2>
    <h1 class="headline title">Where<br>The River<br>Bends Home...</h1>
    <p class="headline when">
      <span class="day">SATURDAY,</span><br>
      <span class="date">JUNE 25, 2022</span><br>
      <span class="time">AT 4 PM</span>
    </p>

    <svg class="paper-edge" viewBox="0 0 818 320" preserveAspectRatio="none" aria-hidden="true">
      <path fill="#ffffff" d="M0 20 L30 14 L70 22 L120 10 L170 18 L200 40 L230 70 L260 110 L300 150 L340 175 L380 190 L420 200 L450 185 L480 160 L520 150 L560 120 L590 105 L620 80 L650 62 L690 50 L720 32 L760 20 L790 10 L818 4 L818 320 L0 320 Z"/>
      <path fill="#ffffff" d="M0 20 L40 60 L60 120 L90 170 L130 200 L180 215 L240 225 L300 205 L340 180 L300 150 L260 110 L230 70 L200 40 L170 18 Z" opacity="0.9"/>
    </svg>

    <div class="venue">
      <p class="venue-name">Kestrel Ridge High School</p>
      <p class="venue-address">31857 Marlow Road Novi, Mi 48291</p>
    </div>

    <div class="studio-mark">
      <span class="studio-dot"></span>
      <p class="studio-name">Brightwing Dance Studio, LLC</p>
    </div>
  </main>
</body>
</html>
```